Rollers & Glides.com

Vertical Business Card with focus on branding with our icon. Information on card will be logo, persons name, position, phone number, email address and website. Use the the name Marcus Pellow, position President, phone number 480.915.2267, email Marcus@rollersandglides-demo.com, website www.rollersandglides-demo.com.

```html
<!DOCTYPE html>
<html lang="en">
<head>
<meta charset="utf-8">
<title>Rollers &amp; Glides.com – Business Card</title>
<link href="https://fonts.googleapis.com/css2?family=Roboto:wght@500;700&family=Arimo:wght@400;700&display=swap" rel="stylesheet">
<style>
  :root {
    --brand-blue: #3561ad;
    --brand-blue-light: #4a72b8;
    --paper: #ffffff;
    --tint: #e9eef6;
    --ink: #1d1d1f;
    --backdrop: #1a1a1a;
    --backdrop-edge: #0b0b0b;
  }
  * { margin: 0; padding: 0; box-sizing: border-box; }
  html, body { width: 1200px; height: 1015px; overflow: hidden; }
  body {
    background: radial-gradient(ellipse at center, var(--backdrop) 0%, var(--backdrop-edge) 100%);
    position: relative;
    font-family: "Arimo", Arial, sans-serif;
  }
  .card {
    position: absolute;
    width: 560px;
    height: 320px;
    overflow: hidden;
    box-shadow: 0 18px 40px rgba(0,0,0,.6);
  }
  .card-front { left: 90px; top: 150px; background: var(--brand-blue); }
  .card-back  { left: 550px; top: 545px; background: var(--paper); }

  .backdrop-circle {
    position: absolute;
    border-radius: 50%;
  }
  .card-front .backdrop-circle {
    width: 300px; height: 300px; right: -60px; top: -70px;
    border: 46px solid var(--brand-blue-light);
  }
  .card-back .backdrop-circle {
    width: 300px; height: 300px; right: -60px; top: -70px;
    border: 46px solid var(--tint);
  }

  .front-mark {
    position: absolute; left: 200px; top: 80px;
    width: 62px; height: 62px; border-radius: 50%;
    background: var(--paper);
  }
  .front-name {
    position: absolute; left: 0; right: 0; top: 170px;
    text-align: center;
    font-family: "Roboto", Arial, sans-serif;
    font-weight: 500; font-size: 30px; letter-spacing: 2px;
    color: var(--paper);
  }

  .back-mark {
    position: absolute; left: 46px; top: 52px;
    width: 42px; height: 42px; border-radius: 50%;
    background: var(--brand-blue);
  }
  .back-brand {
    position: absolute; left: 110px; top: 54px;
    font-family: "Roboto", Arial, sans-serif;
    font-weight: 500; font-size: 28px; letter-spacing: 2px;
    color: var(--brand-blue);
  }
  .person { position: absolute; left: 160px; top: 128px; }
  .person-name {
    font-weight: 700; font-size: 20px; color: var(--brand-blue);
    text-transform: uppercase; letter-spacing: .3px;
  }
  .person-title { font-size: 15px; color: var(--ink); margin-top: 2px; }
  .contacts { position: absolute; left: 172px; top: 200px; list-style: none; }
  .contacts li {
    display: flex; align-items: center; gap: 8px;
    font-size: 14px; color: var(--ink); line-height: 24px;
  }
  .contacts svg { width: 14px; height: 14px; fill: var(--brand-blue); flex: none; }
  .accent { color: var(--brand-blue); }
</style>
</head>
<body>
  <section class="card card-front" aria-label="Business card front">
    <div class="backdrop-circle"></div>
    <div class="front-mark"></div>
    <p class="front-name">Rollers &amp; Glides.com</p>
  </section>

  <section class="card card-back" aria-label="Business card back">
    <div class="backdrop-circle"></div>
    <div class="back-mark"></div>
    <p class="back-brand">Rollers &amp; Glides.com</p>
    <div class="person">
      <p class="person-name">Marcus Pellow</p>
      <p class="person-title">President</p>
    </div>
    <ul class="contacts">
      <li>
        <svg viewBox="0 0 24 24"><path d="M6.6 10.8a15 15 0 0 0 6.6 6.6l2.2-2.2a1 1 0 0 1 1-.25 11.4 11.4 0 0 0 3.6.57 1 1 0 0 1 1 1V20a1 1 0 0 1-1 1A17 17 0 0 1 3 4a1 1 0 0 1 1-1h3.5a1 1 0 0 1 1 1c0 1.25.2 2.45.57 3.57a1 1 0 0 1-.25 1z"/></svg>
        480.915.2267
      </li>
      <li>
        <svg viewBox="0 0 24 24"><path d="M2 5h20v14H2z M3 6l9 7 9-7" fill="none" stroke="currentColor"/><path d="M2 5h20v14H2zm2 2v.2l8 6 8-6V7l-8 6z"/></svg>
        Marcus@rollersandglides-demo.com
      </li>
      <li>
        <svg viewBox="0 0 24 24"><circle cx="12" cy="12" r="10" fill="none" stroke="#3561ad" stroke-width="2"/><path d="M2 12h20M12 2c3 3 3 17 0 20M12 2c-3 3-3 17 0 20" fill="none" stroke="#3561ad" stroke-width="1.6"/></svg>
        <span>www.<span class="accent">rollersandglides-demo</span>.com</span>
      </li>
    </ul>
  </section>
</body>
</html>
```